KPL Construction we build lodges in Botswana

We need a Design Layout only with Categories where we can update each projects photos.... We have a web address and a host - kpl.construction

```html
<!DOCTYPE html>
<html lang="en">
<head>
<meta charset="UTF-8">
<title>KPL Construction</title>
<link href="https://fonts.googleapis.com/css2?family=Poppins:wght@300;400;500;600;700&display=swap" rel="stylesheet">
<style>
:root{
  --teal:#3f8f88;
  --teal-dark:#2e6f69;
  --ink:#2b2b2b;
  --muted:#8a8a8a;
  --white:#ffffff;
  --light:#f3f3f3;
  --footer:#2a2a2a;
  --footer-text:#a9a9a9;
}
*{margin:0;padding:0;box-sizing:border-box}
html,body{width:1200px;height:3336px;overflow:hidden}
body{font-family:'Poppins',sans-serif;color:var(--ink);background:var(--white);position:relative}
.canvas{position:relative;width:1200px;height:3336px;overflow:hidden}

/* Hero */
.hero{position:absolute;top:0;left:0;width:1200px;height:600px}
.hero-photo{position:absolute;inset:0;background:linear-gradient(180deg,#4a5663 0%,#8b7a66 35%,#d99a5a 60%,#6a4b33 85%,#3b2b20 100%)}
.site-header{position:absolute;top:0;left:0;right:0;height:70px;display:flex;align-items:center;padding:0 170px;color:var(--white)}
.brand{display:flex;align-items:center;gap:10px;font-weight:600;font-size:19px;letter-spacing:.5px;text-transform:uppercase}
.brand-mark{width:22px;height:22px;background:var(--teal)}
.main-nav{display:flex;gap:34px;margin-left:auto;font-size:14px}
.main-nav a{color:var(--white);text-decoration:none}
.call{display:flex;align-items:center;gap:10px;margin-left:40px}
.call-text{font-size:11px;line-height:1.2;text-align:right}
.call-text strong{display:block;font-size:15px;font-weight:600}
.call-icon{width:30px;height:30px;border-radius:50%;background:var(--teal);display:flex;align-items:center;justify-content:center}
.hero-copy{position:absolute;top:255px;left:0;right:0;text-align:center;color:var(--white)}
.hero-copy h1{font-size:44px;font-weight:600}
.hero-copy p{font-size:14px;line-height:1.6;margin-top:14px}
.btn{display:inline-block;background:var(--teal);color:var(--white);font-size:12px;font-weight:500;text-transform:uppercase;padding:11px 28px;border-radius:3px;letter-spacing:.5px}
.hero-copy .btn{margin-top:32px}

/* Shared section heads */
.section-title{text-align:center;font-size:33px;font-weight:500;color:var(--ink)}
.section-lead{text-align:center;font-size:12px;line-height:1.7;color:var(--muted);margin:22px auto 0;width:820px}

/* Welcome */
.welcome{position:absolute;top:600px;left:0;width:1200px;height:560px;border-top:1px solid #e6e6e6}
.welcome .section-title{margin-top:60px}
.feature-cards{display:flex;gap:30px;width:860px;margin:46px auto 0}
.feature-card{width:267px}
.feature-photo{height:155px}
.feature-card h3{display:flex;justify-content:space-between;font-size:14px;font-weight:500;margin-top:20px}
.feature-card p{font-size:11px;line-height:1.7;color:var(--muted);margin-top:10px}

/* Projects */
.projects{position:absolute;top:1160px;left:0;width:1200px;height:800px}
.projects .section-title{margin-top:62px}
.project-grid{position:absolute;top:200px;left:0;width:1200px;height:572px}
.project{position:absolute}
.project-overlay{position:absolute;left:0;right:0;bottom:0;height:90px;background:rgba(0,0,0,.55);color:var(--white);padding:20px 24px}
.project-overlay h4{font-size:15px;font-weight:500;text-transform:uppercase;letter-spacing:1px}
.project-overlay p{font-size:10px;margin-top:6px;color:#ddd}

/* Why choose */
.why{position:absolute;top:1960px;left:0;width:1200px;height:700px}
.why .section-title{margin-top:92px}
.why .section-lead{margin-top:14px}
.why-photo{position:absolute;top:380px;left:0;width:1200px;height:320px;background:linear-gradient(180deg,#ffffff 0%,#e9ecef 30%,#4f6a45 70%,#3a4e33 100%)}
.why-boxes{position:absolute;top:180px;left:170px;display:flex;gap:40px}
.why-box{width:205px;height:280px;background:var(--white);text-align:center;padding-top:46px;position:relative}
.why-box.active{border:2px solid var(--teal)}
.why-icon{width:68px;height:68px;border-radius:50%;border:2px solid var(--teal);margin:0 auto;display:flex;align-items:center;justify-content:center}
.why-box.active .why-icon{background:var(--teal)}
.why-box h3{font-size:14px;font-weight:500;margin-top:28px}
.why-box p{font-size:10px;line-height:1.7;color:var(--muted);margin:10px 18px 0}
.why-box .btn{position:absolute;bottom:-14px;left:50%;transform:translateX(-50%);font-size:10px;padding:8px 20px}

/* Testimonials */
.testimonials{position:absolute;top:2660px;left:0;width:1200px;height:340px;background:var(--light);text-align:center}
.testimonials .section-title{margin-top:58px}
.quote{width:840px;margin:32px auto 0;font-size:12px;line-height:1.9;color:#555}
.quote-mark{color:var(--teal);font-weight:700}
.author{margin-top:18px;font-size:15px;font-style:normal;color:var(--teal);font-weight:500}

/* Footer */
.site-footer{position:absolute;top:3000px;left:0;width:1200px;height:336px;background:var(--footer);color:var(--footer-text)}
.footer-cols{display:flex;justify-content:space-between;width:1030px;margin:38px auto 0}
.footer-col h5{color:var(--white);font-size:15px;font-weight:500;margin-bottom:16px}
.footer-col li{list-style:none;font-size:11px;line-height:2}
.social{display:flex;gap:12px;margin-bottom:26px}
.social span{width:18px;height:18px;border-radius:50%;background:var(--white)}
.footer-bottom{position:absolute;bottom:0;left:0;right:0;height:60px;border-top:1px solid #3a3a3a;font-size:11px;text-align:center;line-height:60px}
</style>
</head>
<body>
<div class="canvas">

  <section class="hero">
    <div class="hero-photo" role="img" aria-label="Builders on a timber frame silhouetted against a sunset sky"></div>
    <header class="site-header">
      <div class="brand"><span class="brand-mark"></span>KPL Construction</div>
      <nav class="main-nav">
        <a href="#">Home</a><a href="#">About us</a><a href="#">Projects</a><a href="#">Blog</a><a href="#">Contact Us</a>
      </nav>
      <div class="call">
        <div class="call-text">CALL<strong>555 014 2210</strong></div>
        <div class="call-icon">
          <svg width="14" height="14" viewBox="0 0 24 24"><path d="M6.6 10.8a15 15 0 0 0 6.6 6.6l2.2-2.2a1 1 0 0 1 1-.25 11.4 11.4 0 0 0 3.6.6 1 1 0 0 1 1 1V20a1 1 0 0 1-1 1A17 17 0 0 1 3 4a1 1 0 0 1 1-1h3.5a1 1 0 0 1 1 1c0 1.25.2 2.45.6 3.6a1 1 0 0 1-.25 1z" fill="#fff"/></svg>
        </div>
      </div>
    </header>
    <div class="hero-copy">
      <h1>KPL Construction</h1>
      <p>We're a Construction Company based in Botswana.<br>Builders and specialists in Lodge Building</p>
      <span class="btn">Get Started</span>
    </div>
  </section>

  <section class="welcome">
    <h2 class="section-title">Welcome to KPL Construction</h2>
    <p class="section-lead">We design and build timber lodges across Botswana, from small bush cabins to full safari camps. Our team handles planning, materials and building so every lodge is finished on time and made to last for years.</p>
    <div class="feature-cards">
      <article class="feature-card">
        <div class="feature-photo" role="img" aria-label="Warm timber lodge interior with wooden walls" style="background:linear-gradient(135deg,#b5825a,#6e4a30)"></div>
        <h3>Finibus Bonorum <span>&rarr;</span></h3>
        <p>Hand built timber interiors with open living rooms, warm finishes and views over the surrounding bush.</p>
      </article>
      <article class="feature-card">
        <div class="feature-photo" role="img" aria-label="Large wooden lodge among tall trees" style="background:linear-gradient(135deg,#5f7a4e,#7b5a3e)"></div>
        <h3>Finibus Bonorum <span>&rarr;</span></h3>
        <p>Sturdy lodge frames set among the trees, planned around the land and built with local crews.</p>
      </article>
      <article class="feature-card">
        <div class="feature-photo" role="img" aria-label="Builders reviewing plans at a site" style="background:linear-gradient(135deg,#8fa3b5,#4d5d6c)"></div>
        <h3>Finibus Bonorum <span>&rarr;</span></h3>
        <p>Careful planning with clients at every step, from first drawings through to the final handover.</p>
      </article>
    </div>
  </section>

  <section class="projects">
    <h2 class="section-title">Our Recent Projects</h2>
    <p class="section-lead">Browse our latest lodges by category. Each project page holds fresh photos from the build,<br>showing the work from the first post to the finished lodge.</p>
    <div class="project-grid">
      <div class="project" style="left:0;top:0;width:592px;height:280px;background:linear-gradient(135deg,#7a4a2a,#5d7a3e)" role="img" aria-label="Two storey log lodge with green lawn"></div>
      <div class="project" style="left:600px;top:0;width:296px;height:280px;background:linear-gradient(135deg,#5a4a3a,#8a6a4a)" role="img" aria-label="Timber lodge with porch and trees"></div>
      <div class="project" style="left:904px;top:0;width:296px;height:280px;background:linear-gradient(135deg,#3e5a3a,#a3704a)" role="img" aria-label="Log lodge lit at dusk"></div>
      <div class="project" style="left:0;top:292px;width:288px;height:280px;background:linear-gradient(135deg,#8a5a3a,#4e7a3a)" role="img" aria-label="Wooden chalet on a green slope"></div>
      <div class="project" style="left:300px;top:292px;width:292px;height:280px;background:linear-gradient(135deg,#a86a4a,#6a8a4a)" role="img" aria-label="Brick and timber house with tall windows"></div>
      <div class="project" style="left:608px;top:292px;width:592px;height:280px;background:linear-gradient(135deg,#2e2620,#7a5634)" role="img" aria-label="Lodge interior with glowing lights at night">
        <div class="project-overlay">
          <h4>Sed Utperspiciatiund</h4>
          <p>Riverside lodge finished with local hardwood floors</p>
        </div>
      </div>
    </div>
  </section>

  <section class="why">
    <div class="why-photo" role="img" aria-label="Wooden lodge with green roof among pine trees"></div>
    <h2 class="section-title">Why Choose Us?</h2>
    <p class="section-lead">Trusted lodge builders with skilled crews and honest prices</p>
    <div class="why-boxes">
      <div class="why-box">
        <div class="why-icon"><svg width="30" height="30" viewBox="0 0 30 30" fill="none" stroke="#3f8f88" stroke-width="2"><rect x="4" y="6" width="22" height="18"/><path d="M8 12h14M8 17h10"/></svg></div>
        <h3>Finibus Bonorum</h3>
        <p>Clear plans and drawings before any work begins on site.</p>
      </div>
      <div class="why-box active">
        <div class="why-icon"><svg width="30" height="30" viewBox="0 0 30 30" fill="none" stroke="#fff" stroke-width="2"><rect x="5" y="5" width="20" height="20"/><path d="M10 15l4 4 7-8"/></svg></div>
        <h3>Finibus Bonorum</h3>
        <p>Quality checks at every stage of the lodge build.</p>
        <span class="btn">Read More</span>
      </div>
      <div class="why-box">
        <div class="why-icon"><svg width="30" height="30" viewBox="0 0 30 30" fill="none" stroke="#3f8f88" stroke-width="2"><path d="M8 4h11l5 5v17H8z"/><path d="M12 15h8M12 20h8"/></svg></div>
        <h3>Finibus Bonorum</h3>
        <p>Fair fixed quotes with no hidden costs at the end.</p>
      </div>
      <div class="why-box">
        <div class="why-icon"><svg width="30" height="30" viewBox="0 0 30 30" fill="none" stroke="#3f8f88" stroke-width="2"><path d="M6 26V10h8v16M14 26V4h10v22M4 26h22"/></svg></div>
        <h3>Finibus Bonorum</h3>
        <p>Local crews who know the land and the climate well.</p>
      </div>
    </div>
  </section>

  <section class="testimonials">
    <h2 class="section-title">Testimonials</h2>
    <p class="quote"><span class="quote-mark">&ldquo;</span> KPL Construction built our safari lodge near the delta and the result is better than we imagined. The team listened to every idea, kept us updated with photos each week and finished the build on time. The timber work is beautiful and guests always ask who built it. We would gladly work with them again on our next camp and recommend them to anyone planning a lodge. <span class="quote-mark">&rdquo;</span></p>
    <p class="author">Kago Molefe, Botswana</p>
  </section>

  <footer class="site-footer">
    <div class="footer-cols">
      <div class="footer-col"><h5>About</h5><ul><li>Our story</li><li>Our team</li><li>Careers</li><li>Lodge building</li></ul></div>
      <div class="footer-col"><h5>Nav Links</h5><ul><li>Home</li><li>About us</li><li>Projects</li><li>Blog</li><li>Contact us</li></ul></div>
      <div class="footer-col"><h5>Projects</h5><ul><li>Safari lodges</li><li>Bush cabins</li><li>River camps</li><li>Guest houses</li><li>Renovations</li></ul></div>
      <div class="footer-col"><h5>Connect</h5>
        <div class="social"><span></span><span></span><span></span><span></span></div>
        <h5>Policies</h5><ul><li>Privacy</li><li>Terms and feedback</li></ul></div>
      <div class="footer-col"><h5>Other Links</h5><ul><li>Site updates</li><li>Building guide</li><li>Materials</li><li>Photo gallery</li><li>Get a quote</li></ul></div>
    </div>
    <div class="footer-bottom">&copy; 2024 KPL Construction. All rights are reserved. Privacy Policy | Terms of Use | Contact</div>
  </footer>

</div>
</body>
</html>
```